Quillmarsh Property Solutions need a business card design

Hello guys. We would need a business card design asap please.
We are a start up property investment business based in London UK specialised in buying, selling, managing and letting properties and helping distressed property owners.
The name of our Business is Quillmarsh, the logo symbolises the four fundamental elements of the world (earth, air, fire and water) and so it stands for strength, stability, longevity.
We would like the business card to communicate professionalism and reliability. Many many thanks indeed for your work.

Details:

1.) Rosalind Updike
Property Investor
Mobile: +44(0)7700123456
Email: rosalind.quillmarsh@mailbox-example.com

2.) Dominic Updike
Property Investor
Mobile: +44(0)7700987654
Email: dominic.quillmarsh@mailbox-example.com

```html
<!DOCTYPE html>
<html lang="en">
<head>
<meta charset="utf-8">
<title>Quillmarsh Property Solutions – Business Card</title>
<link rel="stylesheet" href="https://fonts.googleapis.com/css2?family=Josefin+Sans:wght@700&family=Open+Sans:wght@400;600&display=swap">
<style>
  :root {
    --page-bg: #d6d6d8;
    --card-white: #ffffff;
    --mist-light: #ffffff;
    --mist-dark: #c9d6d5;
    --ink-dark: #4a4a4c;
    --ink-body: #333333;
    --name-blue: #2f57b0;
    --role-green: #208a3c;
    --icon-red: #d6313d;
    --band-green: #1f8a43;
    --band-blue: #2f5bb0;
    --band-red: #d23441;
  }
  * { box-sizing: border-box; margin: 0; padding: 0; }
  html, body {
    width: 883px;
    height: 1200px;
    overflow: hidden;
    background: var(--page-bg);
    font-family: "Open Sans", Arial, sans-serif;
  }
  .sheet {
    width: 883px;
    height: 1200px;
    display: flex;
    flex-direction: column;
    align-items: center;
    justify-content: center;
    gap: 40px;
  }
  .card {
    position: relative;
    width: 600px;
    height: 336px;
    background: var(--card-white);
    overflow: hidden;
    box-shadow: 0 2px 6px rgba(0,0,0,0.12);
  }
  .colour-band {
    position: absolute;
    right: 0;
    bottom: 0;
    width: 324px;
    height: 27px;
    display: flex;
  }
  .colour-band span { flex: 1; }
  .colour-band .green { background: var(--band-green); }
  .colour-band .blue { background: var(--band-blue); }
  .colour-band .red { background: var(--band-red); }

  /* Front */
  .card-front {
    background: radial-gradient(ellipse at 35% 30%, var(--mist-light) 0%, #eef2f2 45%, var(--mist-dark) 100%);
  }
  .hero-photo {
    position: absolute;
    left: 0;
    top: 40px;
    width: 380px;
    height: 296px;
    background: linear-gradient(160deg, #3b3b3d 0%, #8c857d 35%, #e6d9cc 60%, #d9b9a0 85%, #c79d84 100%);
    opacity: 0.85;
  }
  .front-wordmark {
    position: absolute;
    left: 338px;
    top: 138px;
    color: var(--ink-dark);
    font-family: "Josefin Sans", "Open Sans", sans-serif;
    font-weight: 700;
  }
  .front-wordmark .name { font-size: 31px; letter-spacing: 0.5px; line-height: 1; }
  .front-wordmark .tagline { font-size: 15px; margin-top: 8px; padding-left: 20px; letter-spacing: 0.3px; }

  /* Back */
  .back-brand {
    position: absolute;
    left: 38px;
    top: 72px;
    width: 210px;
    text-align: center;
    color: var(--ink-dark);
    font-family: "Josefin Sans", "Open Sans", sans-serif;
    font-weight: 700;
  }
  .brand-dot {
    width: 100px;
    height: 100px;
    border-radius: 50%;
    background: var(--ink-dark);
    margin: 0 auto 14px;
  }
  .back-brand .name { font-size: 29px; letter-spacing: 0.5px; line-height: 1; }
  .back-brand .tagline { font-size: 14px; margin-top: 6px; letter-spacing: 0.3px; }

  .contacts {
    position: absolute;
    left: 283px;
    top: 52px;
  }
  .contact + .contact { margin-top: 22px; }
  .contact .person { color: var(--name-blue); font-size: 20px; line-height: 26px; padding-left: 29px; }
  .contact .role { color: var(--role-green); font-size: 15px; line-height: 22px; padding-left: 29px; }
  .contact .line {
    display: flex;
    align-items: center;
    gap: 11px;
    color: var(--ink-body);
    font-size: 15px;
    line-height: 23px;
  }
  .contact .line svg { width: 18px; height: 14px; flex: none; }
</style>
</head>
<body>
<main class="sheet">

  <section class="card card-front" aria-label="Business card front">
    <div class="hero-photo" role="img" aria-label="Photo of an open hand holding a small model house"></div>
    <div class="front-wordmark">
      <div class="name">QUILLMARSH</div>
      <div class="tagline">PROPERTY SOLUTIONS</div>
    </div>
    <div class="colour-band"><span class="green"></span><span class="blue"></span><span class="red"></span></div>
  </section>

  <section class="card card-back" aria-label="Business card back">
    <div class="back-brand">
      <div class="brand-dot"></div>
      <div class="name">QUILLMARSH</div>
      <div class="tagline">PROPERTY SOLUTIONS</div>
    </div>

    <div class="contacts">
      <div class="contact">
        <div class="person">Dominic Updike</div>
        <div class="role">Property Investor</div>
        <div class="line">
          <svg viewBox="0 0 18 14" aria-hidden="true"><path fill="var(--icon-red)" d="M1 4c0-2 3-3 8-3s8 1 8 3v1h-4V3.5H5V5H1z M4 6h10l2 7H2z"/><circle cx="9" cy="9.5" r="2" fill="#fff"/></svg>
          <span>+44(0)7700987654</span>
        </div>
        <div class="line">
          <svg viewBox="0 0 18 14" aria-hidden="true"><rect x="1" y="1.5" width="16" height="11" fill="var(--icon-red)"/><path d="M1.5 2l7.5 6 7.5-6" fill="none" stroke="#fff" stroke-width="1.4"/></svg>
          <span>dominic.quillmarsh@mailbox-example.com</span>
        </div>
      </div>

      <div class="contact">
        <div class="person">Rosalind Updike</div>
        <div class="role">Property Investor</div>
        <div class="line">
          <svg viewBox="0 0 18 14" aria-hidden="true"><path fill="var(--icon-red)" d="M1 4c0-2 3-3 8-3s8 1 8 3v1h-4V3.5H5V5H1z M4 6h10l2 7H2z"/><circle cx="9" cy="9.5" r="2" fill="#fff"/></svg>
          <span>+44(0)7700123456</span>
        </div>
        <div class="line">
          <svg viewBox="0 0 18 14" aria-hidden="true"><rect x="1" y="1.5" width="16" height="11" fill="var(--icon-red)"/><path d="M1.5 2l7.5 6 7.5-6" fill="none" stroke="#fff" stroke-width="1.4"/></svg>
          <span>rosalind.quillmarsh@mailbox-example.com</span>
        </div>
      </div>
    </div>

    <div class="colour-band"><span class="green"></span><span class="blue"></span><span class="red"></span></div>
  </section>

</main>
</body>
</html>
```